Velk Partners Building Business Cards

We need a business card that reflects our business as "Solar Experts" in San Diego. Browse our website www.velkpartners.example our License needs to be displayed as "CSLB# 3867140" our phone number is (619) 555-0187

Save thousands on your electric bills and increase the value of your home while helping to protect the environment. Our solar installation experts will help you design the system that's right for you, using only the highest quality equipment that will look great and give you ideal performance. Our goal is to make you energy independent, and get your electric bill to 0.

Paul Osterby
(619) 555-0187
paul@velkpartners.example

Target Market(s)

Home owners in san diego looking for solar

Industry/Entity Type

Solar Energy

Contact Information for Business Card

Paul Osterby
(619) 555-0187
paul@velkpartners.example

Font styles to use
Other font styles liked:
• Use our logo font

Requirements
Must have
• License needs to be displayed as "CSLB# 3867140" our phone number is (619) 555-0187
Nice to have
• Real images of rooftop home solar in san diego
Should not have
• our business address

```html
<!DOCTYPE html>
<html lang="en">
<head>
<meta charset="utf-8">
<title>Velk Partners Building – Business Card</title>
<link href="https://fonts.googleapis.com/css2?family=Source+Sans+3:wght@400;600;700&display=swap" rel="stylesheet">
<style>
  :root {
    --navy: #1f4688;
    --navy-deep: #173a73;
    --sun: #f6ab00;
    --paper: #ffffff;
    --stage: #e9e6e1;
    --ink-light: #ffffff;
  }
  * { box-sizing: border-box; margin: 0; padding: 0; }
  html, body {
    width: 1200px; height: 950px; overflow: hidden;
    background: var(--stage);
    font-family: "Source Sans 3", "Myriad Pro", Arial, sans-serif;
  }
  .sheet {
    width: 1200px; height: 950px;
    display: flex; flex-direction: column;
    align-items: center; justify-content: center; gap: 34px;
  }
  .card {
    position: relative;
    width: 760px; height: 434px;
    overflow: hidden;
    box-shadow: 0 6px 18px rgba(0,0,0,.18);
  }
  /* Front */
  .card--front { background: var(--paper); }
  .card__wave { position: absolute; inset: 0; width: 100%; height: 100%; }
  .brand {
    position: absolute; left: 40px; top: 170px; width: 270px;
    color: var(--navy); font-weight: 700;
    display: flex; align-items: center; gap: 12px;
  }
  .brand__dot { width: 22px; height: 22px; border-radius: 50%; background: var(--navy); flex: none; }
  .brand__name { font-size: 31px; line-height: 1.05; letter-spacing: -.3px; }
  .person {
    position: absolute; right: 42px; top: 40px; text-align: right;
  }
  .person__name { color: var(--sun); font-weight: 700; font-size: 27px; }
  .person__role { color: var(--ink-light); font-size: 17px; margin-top: 2px; }
  .contact {
    position: absolute; right: 42px; bottom: 46px;
    list-style: none; text-align: right; color: var(--ink-light);
    font-size: 17px; line-height: 1.75;
  }
  .contact li { display: flex; justify-content: flex-end; align-items: center; gap: 9px; }
  .contact svg { width: 17px; height: 17px; flex: none; }
  .contact__spacer { width: 17px; flex: none; }
  /* Back */
  .card--back { background: var(--sun); }
  .back__url {
    position: absolute; left: 34px; top: 50%;
    transform: translateY(-50%) rotate(90deg); transform-origin: left center;
    left: 52px; top: 60px;
    color: var(--ink-light); font-size: 15px; letter-spacing: 4px; white-space: nowrap;
  }
  .back__brand {
    position: absolute; left: 0; right: 0; top: 0; bottom: 0;
    display: flex; align-items: center; justify-content: center; gap: 18px;
    color: var(--ink-light); font-weight: 700; font-size: 40px;
  }
  .back__dot { width: 34px; height: 34px; border-radius: 50%; background: var(--ink-light); }
</style>
</head>
<body>
<main class="sheet">
  <section class="card card--front" aria-label="Card front">
    <svg class="card__wave" viewBox="0 0 760 434" preserveAspectRatio="none" aria-hidden="true">
      <path d="M318,0 C378,130 232,300 350,434 L760,434 L760,0 Z" fill="var(--sun)"/>
      <path d="M334,0 C394,130 248,300 366,434 L760,434 L760,0 Z" fill="var(--paper)"/>
      <path d="M342,0 C402,130 256,300 374,434 L760,434 L760,0 Z" fill="var(--navy)"/>
      <path d="M560,0 L760,0 L760,434 L660,434 Z" fill="var(--navy-deep)" opacity=".35"/>
    </svg>
    <div class="brand">
      <span class="brand__dot"></span>
      <span class="brand__name">Velk Partners Building</span>
    </div>
    <div class="person">
      <div class="person__name">Paul Osterby</div>
      <div class="person__role">CEO/Founder</div>
    </div>
    <ul class="contact">
      <li>CSLB# 3867140<span class="contact__spacer"></span></li>
      <li>(619) 555-0187
        <svg viewBox="0 0 20 20" aria-hidden="true"><circle cx="10" cy="10" r="10" fill="var(--sun)"/><path d="M6.5 5h2l1 2.5-1.3 1a6 6 0 0 0 3.3 3.3l1-1.3 2.5 1v2a1 1 0 0 1-1 1A8.5 8.5 0 0 1 5.5 6a1 1 0 0 1 1-1z" fill="var(--navy)"/></svg></li>
      <li>paul@velkpartners.example
        <svg viewBox="0 0 20 20" aria-hidden="true"><circle cx="10" cy="10" r="10" fill="var(--sun)"/><rect x="5" y="6.5" width="10" height="7" fill="none" stroke="var(--navy)" stroke-width="1.4"/><path d="M5 6.5l5 4 5-4" fill="none" stroke="var(--navy)" stroke-width="1.4"/></svg></li>
      <li>www.velkpartners.example
        <svg viewBox="0 0 20 20" aria-hidden="true"><circle cx="10" cy="10" r="10" fill="var(--sun)"/><circle cx="10" cy="10" r="5" fill="none" stroke="var(--navy)" stroke-width="1.3"/><path d="M5 10h10M10 5c-2.5 3-2.5 7 0 10M10 5c2.5 3 2.5 7 0 10" fill="none" stroke="var(--navy)" stroke-width="1.1"/></svg></li>
    </ul>
  </section>

  <section class="card card--back" aria-label="Card back">
    <div class="back__url">www.velkpartners.example</div>
    <div class="back__brand">
      <span class="back__dot"></span>
      <span>Velk Partners Building</span>
    </div>
  </section>
</main>
</body>
</html>
```